Brightway Haul & Upkeep Services, are a company that offers a 'one stop shop' pre-move clean up a

I have already selected a logo which I would like on the front of the business cards along with phone numbers, web address and email which are:
0487650392
www.brightwayhaul.com.au
brightwayhaulandupkeep@mailbox.example

On the back of the card I would like to list some of the types of service we offer (clean - move - repairs/maintenance) which are:
CLEAN - windows, gutters, solar panels, driveways/paths, carpets.
MOVE - Small/medium size house/office moves, large item pick-up & delivery, yard clean-up and removal.
General maintenance and repairs.

I would like the blue logo on a gray background.

Thanks

```html
<!DOCTYPE html>
<html lang="en">
<head>
<meta charset="utf-8">
<title>Brightway Haul &amp; Upkeep Services – Business Cards</title>
<link rel="stylesheet" href="https://fonts.googleapis.com/css2?family=Open+Sans:wght@400;600;700&display=swap">
<style>
  :root {
    --stage: #ececec;
    --card-light: #d6d6d6;
    --card-dark: #bfbfbf;
    --card-back: #d9d9d9;
    --brand-blue: #2a6db5;
    --ink: #1e1e1e;
    --rule-dark: #2b2b2b;
    --white: #ffffff;
  }
  * { box-sizing: border-box; margin: 0; padding: 0; }
  html, body {
    width: 1200px;
    height: 369px;
    overflow: hidden;
    background: var(--stage);
    font-family: "Open Sans", Arial, sans-serif;
  }
  .stage { position: relative; width: 1200px; height: 369px; }
  .card {
    position: absolute;
    top: 32px;
    width: 535px;
    height: 306px;
    overflow: hidden;
    box-shadow: 0 2px 6px rgba(0,0,0,0.25);
  }
  .card--front {
    left: 48px;
    background: linear-gradient(135deg, var(--card-dark), var(--card-light));
  }
  .card--back {
    left: 619px;
    background: var(--card-back);
  }
  .brand-name {
    position: absolute;
    left: 0; right: 0;
    top: 92px;
    text-align: center;
    font-weight: 700;
    font-size: 34px;
    line-height: 1.15;
    color: var(--brand-blue);
    padding: 0 40px;
  }
  .contact {
    position: absolute;
    left: 0; right: 0;
    display: flex;
    justify-content: center;
    align-items: center;
    gap: 8px;
    color: var(--ink);
  }
  .contact--phone { top: 202px; font-size: 18px; }
  .contact--email { top: 234px; font-size: 14px; }
  .contact svg { fill: var(--brand-blue); flex: none; }
  .footer-rule {
    position: absolute;
    left: 0; right: 0;
    top: 264px;
    height: 3px;
    background: var(--rule-dark);
  }
  .footer-band {
    position: absolute;
    left: 0; right: 0; bottom: 0;
    height: 33px;
    background: var(--brand-blue);
    color: var(--white);
    font-size: 14px;
    letter-spacing: 2.5px;
    display: flex;
    align-items: center;
    justify-content: center;
  }
  .services-title {
    position: absolute;
    left: 0; right: 0;
    top: 200px;
    text-align: center;
    color: var(--brand-blue);
    font-weight: 700;
    font-size: 21px;
    letter-spacing: 1.5px;
  }
  .services-list {
    position: absolute;
    left: 0; right: 0;
    top: 240px;
    list-style: none;
    text-align: center;
    font-weight: 600;
    font-size: 15px;
    color: var(--ink);
    line-height: 28px;
  }
  .services-list li { display: inline-block; margin: 0 6px; }
  .services-list li::before {
    content: "";
    display: inline-block;
    width: 6px; height: 6px;
    border-radius: 50%;
    background: var(--brand-blue);
    margin-right: 7px;
    vertical-align: middle;
  }
  .services-list .wide { display: block; }
  .services-list .wide-item { display: inline-block; }
</style>
</head>
<body>
<main class="stage">
  <section class="card card--front" aria-label="Card front">
    <h1 class="brand-name">Brightway Haul &amp; Upkeep Services</h1>
    <p class="contact contact--phone">
      <svg width="14" height="14" viewBox="0 0 24 24" aria-hidden="true"><path d="M6.6 10.8a15.1 15.1 0 0 0 6.6 6.6l2.2-2.2a1 1 0 0 1 1-.25 11.4 11.4 0 0 0 3.6.57 1 1 0 0 1 1 1V20a1 1 0 0 1-1 1A17 17 0 0 1 3 4a1 1 0 0 1 1-1h3.5a1 1 0 0 1 1 1c0 1.25.2 2.45.57 3.6a1 1 0 0 1-.25 1z"/></svg>
      <span>0487650392</span>
    </p>
    <p class="contact contact--email">
      <svg width="13" height="10" viewBox="0 0 26 20" aria-hidden="true"><path d="M0 0h26v20H0z M2 3v1l11 7 11-7V3L13 10z" fill-rule="evenodd"/></svg>
      <span>brightwayhaulandupkeep@mailbox.example</span>
    </p>
    <div class="footer-rule"></div>
    <div class="footer-band">www.brightwayhaul.com.au</div>
  </section>

  <section class="card card--back" aria-label="Card back">
    <h2 class="brand-name">Brightway Haul &amp; Upkeep Services</h2>
    <h3 class="services-title">Services we offer</h3>
    <ul class="services-list">
      <li>Clean</li><li>Move</li>
      <span class="wide"><li class="wide-item">General Maintenance And Repairs.</li></span>
    </ul>
  </section>
</main>
</body>
</html>
```